Federal IT Consulting Company - Brisolux Consulting Group

We're seeking a skilled web designer to create a modern, bold, and engaging WordPress website for Brisolux Consulting Group, LLC. Our company specializes in federal IT consulting, and our name is a play on "Brightening Solutions." The website should reflect our expertise in the federal technology marketplace and position us as a trusted partner for clients navigating their IT journey.

contact: info@brisoluxgrp-example.com

Current Status

WordPress is already installed on our hosting account
We have an existing logo (may need modernization)

Design Requirements

Style:

Modern and visually striking design
Bold elements to convey confidence and expertise
Incorporate the concept of "brightening solutions" into the design

Features:

Modern UX sliders for dynamic content presentation
Eye-catching, high-quality images (stock photos to be sourced by the designer)
Responsive design for all devices

Color Scheme:

To be proposed by the designer, should align with our brand and convey trust and technological expertise

Logo:

Evaluate our current logo
Create a transparent background version if needed
Propose modernization if deemed necessary

Accessibility:

Ensure design elements are accessible to users with disabilities
Use high contrast ratios for text and background colors
Provide text alternatives for non-text content

Website Structure
Create the following pages, with the possibility of subpages:

Home
Services
About
Contact

Specific Page Requirements
Home Page

Striking hero section with a clear value proposition
Overview of our services
Client testimonials or trust indicators

Services Page

Detailed list of our IT consulting services
Clear explanation of how we help navigate the federal IT landscape

About Page

Company history and mission
Team highlights (if applicable)
Our approach to federal IT consulting

Contact Page

Contact form
Other contact methods (phone, email)

Technical Requirements

Fully responsive design
SEO best practices implemented
Fast loading times
Integration with necessary plugins (to be discussed)
Training on how to update and maintain the site
Full compliance with Web Content Accessibility Guidelines (WCAG) 2.1 Level AA
Adherence to Section 508 standards for federal website accessibility
Implementation of necessary features for ADA compliance
Updates

Designs look the same

Target Market(s)

US Federal Govt customers looking for IT support.

Industry/Entity Type

IT Consulting

Coding

Coded - Design and coding required

Colors
0054AA
0677BA
7BADD7
CADEEF
E8F1F8
0094D4
00A9DD
6FCCEA
C7EBF8
E9F6FB
00AB8E
00BBA5
67D7C9
C6EFE9
E9F9F6

```html
<!DOCTYPE html>
<html lang="en">
<head>
<meta charset="utf-8">
<title>Brisolux Consulting Group</title>
<link href="https://fonts.googleapis.com/css2?family=Archivo:wght@600;700&family=Open+Sans:wght@400;600;700&display=swap" rel="stylesheet">
<style>
:root{
  --blue:#0094D4;
  --blue-bright:#00A9DD;
  --blue-light:#6FCCEA;
  --blue-pale:#C7EBF8;
  --teal:#00BBA5;
  --teal-dark:#00AB8E;
  --ink:#1d1d1f;
  --text:#4a4a4a;
  --muted:#8a8a8a;
  --line:#d6d6d6;
  --grey-bg:#f4f4f4;
  --footer:#3b3b3d;
  --white:#fff;
}
*{box-sizing:border-box;margin:0;padding:0}
html,body{width:1200px;height:3096px;overflow:hidden}
body{font-family:"Open Sans",sans-serif;color:var(--text);background:var(--white);position:relative}
h2.section-title{font-family:"Archivo",sans-serif;font-weight:700;font-size:35px;color:var(--ink);text-align:center;letter-spacing:.3px}
.title-rule{position:absolute;left:543px;width:114px;height:2px;background:#555}
.title-rule::after{content:"";position:absolute;left:28px;top:-1px;width:58px;height:4px;background:var(--teal)}

/* header */
.site-header{position:absolute;top:0;left:0;width:1200px;height:70px;background:var(--white)}
.brand{position:absolute;left:145px;top:20px;display:flex;align-items:center;gap:8px;font-family:"Archivo",sans-serif;font-weight:700;font-size:27px;color:#1f2d3a;letter-spacing:1px}
.brand-dot{width:22px;height:22px;border-radius:50%;background:var(--blue)}
.main-nav{position:absolute;left:546px;top:25px;display:flex;gap:45px;font-size:15px;color:var(--ink)}
.main-nav .active{color:var(--blue);position:relative}
.main-nav .active::after{content:"";position:absolute;left:0;right:0;bottom:-10px;height:2px;background:var(--blue)}
.login-btn{position:absolute;left:956px;top:16px;width:100px;height:37px;border-radius:19px;background:var(--blue);color:#fff;font-weight:600;font-size:15px;display:flex;align-items:center;justify-content:center;gap:8px}

/* hero */
.hero{position:absolute;top:70px;left:0;width:1200px;height:568px;background:linear-gradient(90deg,#5fc6ea 0%,#8ad6f0 45%,#b9e3f2 100%);overflow:hidden}
.hero-photo{position:absolute;left:560px;top:0;width:640px;height:568px;background:linear-gradient(90deg,rgba(120,200,235,0) 0%,#6d8aa3 25%,#2d3a48 55%,#d8d4cf 100%)}
.hero-kicker{position:absolute;left:145px;top:163px;font-size:12px;font-weight:700;color:var(--ink)}
.hero-title{position:absolute;left:144px;top:195px;font-family:"Archivo",sans-serif;font-weight:700;font-size:42px;color:var(--ink)}
.hero-lead{position:absolute;left:145px;top:260px;width:340px;font-size:17px;line-height:26px;color:var(--ink)}
.btn-outline{position:absolute;display:flex;align-items:center;justify-content:center;gap:12px;border-radius:25px;font-weight:600}
.hero .btn-outline{left:145px;top:340px;width:176px;height:48px;border:2px solid var(--ink);color:var(--ink);font-size:17px}

/* services */
.services-title{position:absolute;top:710px;left:0;width:1200px}
.services-intro{position:absolute;top:800px;left:160px;width:880px;text-align:center;font-size:18px;line-height:35px;color:#555}
.service-card{position:absolute;top:910px;width:218px;height:307px;background:var(--white);box-shadow:0 4px 14px rgba(0,0,0,.06)}
.service-card .photo{height:193px;background:linear-gradient(135deg,#c9d3dc,#6f7f8f)}
.service-card h3{font-weight:400;font-size:16px;color:var(--ink);margin:20px 19px 10px}
.service-card p{font-size:12px;line-height:21px;color:var(--muted);margin:0 19px}
.service-card.featured{top:898px;height:348px;background:var(--blue-bright);box-shadow:0 10px 24px rgba(0,148,212,.3)}
.service-card.featured .photo{height:205px;background:linear-gradient(135deg,#b8c4cf,#45576a)}
.service-card.featured h3,.service-card.featured p{color:#fff}
.service-card .learn{display:flex;align-items:center;gap:8px;margin:14px 17px;color:#fff;font-weight:600;font-size:15px}
.slider-arrow{position:absolute;top:1052px;width:25px;height:25px;border-radius:50%;background:#3d3d3d;display:flex;align-items:center;justify-content:center}

/* about */
.about{position:absolute;top:1322px;left:0;width:1200px;height:430px;background:linear-gradient(90deg,#00a6dc,#0aa9dd 60%,#29b4e2);overflow:hidden}
.about-frame{position:absolute;left:42px;top:44px;width:556px;height:556px;border-radius:50%;border:4px solid #fff}
.about-photo{position:absolute;left:56px;top:58px;width:528px;height:528px;border-radius:50%;background:linear-gradient(135deg,#9fb4c6,#2c3e55 60%,#1d2a3b)}
.about-title{position:absolute;left:689px;top:50px;font-family:"Archivo",sans-serif;font-weight:700;font-size:33px;color:#fff}
.about-rule{position:absolute;left:689px;top:103px;width:92px;height:2px;background:rgba(255,255,255,.6)}
.about-rule::before{content:"";position:absolute;left:0;top:-1px;width:66px;height:4px;background:#fff}
.about-text{position:absolute;left:689px;top:134px;width:365px;font-size:13.5px;line-height:24px;color:#fff;text-align:justify}
.about-text p+p{margin-top:7px}
.about .btn-outline{left:689px;top:338px;width:152px;height:40px;border:2px solid #fff;color:#fff;font-size:15px}

/* testimonials */
.testi-title{position:absolute;top:1835px;left:0;width:1200px}
.testi-card{position:absolute;top:1947px;width:373px;height:187px;border-radius:24px;background:#fff;box-shadow:0 8px 30px rgba(0,0,0,.08);overflow:hidden}
.avatar{position:absolute;left:42px;top:24px;width:64px;height:64px;border-radius:50%;background:linear-gradient(135deg,#c6d0d8,#4a5866)}
.testi-name{position:absolute;left:119px;top:36px;font-weight:700;font-size:16px;color:var(--ink)}
.testi-role{position:absolute;left:119px;top:60px;font-size:11px;color:var(--muted)}
.quote-mark{position:absolute;left:292px;top:20px;font-family:"Archivo",sans-serif;font-size:90px;line-height:1;color:#ececec}
.testi-text{position:absolute;left:39px;top:104px;width:310px;font-size:12px;line-height:22px;color:#666}

/* contact */
.contact{position:absolute;top:2228px;left:0;width:1200px;height:602px;background:var(--grey-bg)}
.contact-panel{position:absolute;left:103px;top:70px;width:417px;height:359px;background:var(--teal)}
.contact-panel .rule{position:absolute;right:130px;top:70px;width:34px;height:3px;background:#fff}
.contact-panel .rule::after{content:"";position:absolute;left:34px;top:1px;width:30px;height:1px;background:#fff}
.contact-kicker{position:absolute;right:130px;top:100px;font-weight:700;font-size:17px;color:#fff}
.contact-slogan{position:absolute;right:130px;top:130px;text-align:right;font-family:"Archivo",sans-serif;font-weight:700;font-size:37px;line-height:42px;color:#fff}
.contact-outline{position:absolute;left:694px;top:89px;width:341px;height:323px;border:4px solid #3a3a3a}
.contact-form{position:absolute;left:433px;top:119px;width:583px;height:405px;background:#fff}
.contact-form h3{position:absolute;left:49px;top:30px;font-family:"Archivo",sans-serif;font-weight:600;font-size:32px;color:var(--ink)}
.field{position:absolute;width:213px}
.field label{display:block;font-size:15px;color:var(--ink)}
.field .value{margin-top:12px;padding:0 2px 12px;font-size:11px;color:#aaa;border-bottom:1px solid var(--line)}
.send-btn{position:absolute;left:465px;top:300px;width:64px;height:64px}

/* footer */
.site-footer{position:absolute;top:2830px;left:0;width:1200px;height:266px;background:var(--footer);color:#fff}
.site-footer .brand{left:142px;top:52px;color:#fff;font-size:32px}
.site-footer .brand-dot{background:#fff;width:26px;height:26px}
.socials{position:absolute;left:191px;top:118px;display:flex;gap:8px}
.socials span{width:29px;height:29px;border-radius:50%;background:#fff}
.socials span:first-child{background:var(--blue)}
.foot-col{position:absolute;top:50px}
.foot-col h4{font-weight:600;font-size:16px;margin-bottom:10px}
.foot-col li{list-style:none;font-size:13px;line-height:24px;margin-left:2px}
.subscribe{position:absolute;left:795px;top:86px;display:flex}
.subscribe .input{width:171px;height:42px;background:#fff;border:1px solid #ddd;font-size:11px;color:#999;padding:14px 20px}
.subscribe .submit{width:90px;height:42px;background:var(--blue);display:flex;align-items:center;justify-content:center;font-weight:600;font-size:15px}
.contact-line{position:absolute;left:795px;display:flex;align-items:center;gap:10px;font-size:13px}
.contact-line b{font-size:14px}
.foot-rule{position:absolute;left:142px;top:212px;width:914px;height:1px;background:#555}
.copyright{position:absolute;left:0;top:236px;width:1200px;text-align:center;font-size:13px}
</style>
</head>
<body>

<header class="site-header">
  <div class="brand"><span class="brand-dot"></span>BRISOLUX</div>
  <nav class="main-nav">
    <span class="active">Home</span><span>About Us</span><span>Services</span><span>Contact</span>
  </nav>
  <div class="login-btn">Login <svg width="8" height="10" viewBox="0 0 8 10"><path d="M2 1l4 4-4 4" fill="none" stroke="#fff" stroke-width="1.6"/></svg></div>
</header>

<section class="hero">
  <div class="hero-photo" role="img" aria-label="Three business professionals walking through a glass office corridor"></div>
  <div class="hero-kicker">Welcome To</div>
  <h1 class="hero-title">BRISOLUX</h1>
  <p class="hero-lead">Lorem ipsum dolor sit amet, consectetur adipiscing elit, sed eiusmod tempor.</p>
  <div class="btn-outline">Get Started
    <svg width="22" height="14" viewBox="0 0 22 14"><path d="M1 7h19M14 1l6 6-6 6" fill="none" stroke="#1d1d1f" stroke-width="2"/></svg></div>
</section>

<section>
  <h2 class="section-title services-title">OUR SERVICES</h2>
  <div class="title-rule" style="top:774px"></div>
  <p class="services-intro">Lorem ipsum dolor sit amet, consectetur adipiscing elit, sed do eiusmod tempor incididunt ut labore et dolore magna aliqua. Ut enim ad minim veniam, quis nostrud exercitation ullamco laboris.</p>

  <div class="slider-arrow" style="left:88px"><svg width="8" height="10" viewBox="0 0 8 10"><path d="M6 1L2 5l4 4" fill="none" stroke="#fff" stroke-width="1.5"/></svg></div>
  <div class="slider-arrow" style="left:1087px"><svg width="8" height="10" viewBox="0 0 8 10"><path d="M2 1l4 4-4 4" fill="none" stroke="#fff" stroke-width="1.5"/></svg></div>

  <article class="service-card" style="left:145px">
    <div class="photo" role="img" aria-label="Colleagues reviewing a tablet in an office"></div>
    <h3>Lorem ipsum dolor</h3><p>Sed ut perspiciatis unde omnis iste natus error sit volupta</p>
  </article>
  <article class="service-card featured" style="left:375px">
    <div class="photo" role="img" aria-label="Team gathered around a meeting table"></div>
    <h3>Lorem ipsum dolor</h3><p>Sed ut perspiciatis unde omnis iste natus error sit volupta</p>
    <div class="learn">Learn More <svg width="7" height="10" viewBox="0 0 7 10"><path d="M1 1l4 4-4 4" fill="none" stroke="#fff" stroke-width="1.6"/></svg></div>
  </article>
  <article class="service-card" style="left:606px">
    <div class="photo" role="img" aria-label="Group working together at a laptop" style="background:linear-gradient(135deg,#d6dde4,#8a98a6)"></div>
    <h3>Lorem ipsum dolor</h3><p>Sed ut perspiciatis unde omnis iste natus error sit volupta</p>
  </article>
  <article class="service-card" style="left:836px">
    <div class="photo" role="img" aria-label="Two professionals holding documents" style="background:linear-gradient(135deg,#e4e4e4,#6a6e78)"></div>
    <h3>Lorem ipsum dolor</h3><p>Sed ut perspiciatis unde omnis iste natus error sit volupta</p>
  </article>
</section>

<section class="about">
  <div class="about-frame"></div>
  <div class="about-photo" role="img" aria-label="Two consultants discussing work on a tablet"></div>
  <h2 class="about-title">ABOUT US</h2>
  <div class="about-rule"></div>
  <div class="about-text">
    <p>Lorem ipsum dolor sit amet, consectetur adipiscing elit, sed do eiusmod tempor incididunt ut labore et dolore magna aliqua. Ut enim ad minim veniam, quis nostrud exercitation ullamco laboris nisi ut aliquip.</p>
    <p>Duis aute irure dolor in reprehenderit in voluptate velit esse cillum dolore eu fugiat nulla pariatur. Excepteur sint occaecat cupidatat non proident,</p>
  </div>
  <div class="btn-outline">Read More
    <svg width="18" height="12" viewBox="0 0 18 12"><path d="M1 6h15M11 1l5 5-5 5" fill="none" stroke="#fff" stroke-width="1.8"/></svg></div>
</section>

<section>
  <h2 class="section-title testi-title">TESTIMONIALS</h2>
  <div class="title-rule" style="top:1900px"></div>

  <article class="testi-card" style="left:145px">
    <div class="avatar" role="img" aria-label="Portrait of Owen Harlow"></div>
    <div class="testi-name">Owen Harlow</div><div class="testi-role">Lorem ipsum</div>
    <div class="quote-mark">“</div>
    <p class="testi-text">Lorem ipsum dolor sit amet, consectetur adipiscing elit, sed do eiusmod tempor incididunt ut labore et dolore magna aliqua, Ut enim ad minim.</p>
  </article>
  <article class="testi-card" style="left:539px">
    <div class="avatar" role="img" aria-label="Portrait of Mira Castell"></div>
    <div class="testi-name">Mira Castell</div><div class="testi-role">Lorem ipsum</div>
    <div class="quote-mark">“</div>
    <p class="testi-text">Lorem ipsum dolor sit amet, consectetur adipiscing elit, sed do eiusmod tempor incididunt ut labore et dolore magna aliqua, Ut enim ad minim.</p>
  </article>
  <article class="testi-card" style="left:934px">
    <div class="avatar" role="img" aria-label="Portrait of Dean Volkov"></div>
    <div class="testi-name">Dean Volkov</div><div class="testi-role">Lorem ipsum</div>
    <div class="quote-mark">“</div>
    <p class="testi-text">Lorem ipsum dolor sit amet, consectetur adipiscing elit, sed do eiusmod tempor incididunt ut labore et dolore magna aliqua, Ut enim ad minim.</p>
  </article>
</section>

<section class="contact">
  <div class="contact-panel">
    <div class="rule"></div>
    <div class="contact-kicker">CONTACT US</div>
    <div class="contact-slogan">Let’s Do<br>Good<br>Together!</div>
  </div>
  <div class="contact-outline"></div>
  <form class="contact-form">
    <h3>Send Us A Message</h3>
    <div class="field" style="left:53px;top:106px"><label>Your Name</label><div class="value">John Smith</div></div>
    <div class="field" style="left:310px;top:106px"><label>Company</label><div class="value">Lorem Ipsum</div></div>
    <div class="field" style="left:53px;top:192px"><label>Email Address</label><div class="value">info@example.com</div></div>
    <div class="field" style="left:310px;top:192px"><label>Phone</label><div class="value">0123-456-7890</div></div>
    <div class="field" style="left:53px;top:280px;width:420px"><label>Message</label><div class="value" style="padding-bottom:30px">Lorem ipsum dolor sit amet, .....</div></div>
    <svg class="send-btn" viewBox="0 0 64 64" aria-label="Send">
      <circle cx="32" cy="32" r="30" fill="var(--blue-bright)"/>
      <path d="M20 33l22-11-6 22-5-7-4 4 1-6z" fill="#fff"/>
    </svg>
  </form>
</section>

<footer class="site-footer">
  <div class="brand"><span class="brand-dot"></span>BRISOLUX</div>
  <div class="socials"><span></span><span></span><span></span></div>
  <div class="foot-col" style="left:411px"><h4>QUICK LINKS</h4><ul><li>Home</li><li>About Us</li><li>Services</li><li>Contact</li></ul></div>
  <div class="foot-col" style="left:585px"><h4>OTHER LINKS</h4><ul><li>Terms of Services</li><li>Terms &amp; Condition</li><li>Privacy Policy</li></ul></div>
  <div class="foot-col" style="left:791px"><h4 style="font-size:17px">SUBSCRIBE FOR UPDATES</h4></div>
  <div class="subscribe"><div class="input">Email Address</div><div class="submit">Submit</div></div>
  <div class="contact-line" style="top:150px">
    <svg width="13" height="10" viewBox="0 0 13 10"><rect width="13" height="10" rx="1" fill="var(--blue)"/><path d="M0 1l6.5 5L13 1" fill="none" stroke="#3b3b3d" stroke-width="1.2"/></svg>
    <span><b>Email :</b> info@brisolux-example.com</span></div>
  <div class="contact-line" style="top:178px">
    <svg width="13" height="13" viewBox="0 0 13 13"><path d="M3 1l2 3-1.5 1.5a8 8 0 0 0 4 4L9 8l3 2-1.5 2.5C5 12 1 8 .5 2.5z" fill="var(--blue)"/></svg>
    <span><b>Phone :</b> 1+888-555-0142</span></div>
  <div class="foot-rule"></div>
  <div class="copyright">2024 Copyright - BRISOLUX | All Rights Reserved</div>
</footer>

</body>
</html>
```